KorvaLex Injury Solicitors

We need a modern, sleek letterhead that is professional.

In relation to the footer, we would like to have firm contact details there ideally, however you must also insert at the bottom of each page the following....

Liability limited by a scheme approved under the Professional Standards Legislation.

From the attachment you can extract the firm logo. Also, I would like the Accredited specialist circle on the letterhead also.

Also, I would like you to create a document that can easily be edited for change of contact details, as these are likely to change.

Industry/Entity Type

It Professional

Font styles to use
Sans Serif

Colors
0655a3
3276b5
85abd2
0492cd
33a6d7
85cae6
cee9f5
eaf1f7
cbcbcb

Requirements
Must have
• Ph: 9317-5802
• F: 9581-3274
• M 0438-615-249
• mt@korvalex.com.au
• www.korvalex.com.au
Nice to have
• the word document gives you an idea of what I like. I am happy for your to amaze me with your creativity.

```html
<!DOCTYPE html>
<html lang="en">
<head>
<meta charset="utf-8">
<title>KorvaLex Injury Solicitors — Letterhead</title>
<link rel="stylesheet" href="https://fonts.googleapis.com/css2?family=Cinzel:wght@600&family=Arimo:wght@400&family=Questrial&display=swap">
<style>
  :root {
    --backdrop: #e4e4e4;
    --paper: #ffffff;
    --ink: #1b1b1b;
    --ink-soft: #3a3a3a;
    --brand-deep: #0655a3;
    --brand-mid: #3276b5;
    --rule: #33a6d7;
    --seal-ring: #cfd8ec;
    --footer-wash: #eaf1f7;
  }
  * { margin: 0; padding: 0; box-sizing: border-box; }
  html, body {
    width: 1000px; height: 1200px; overflow: hidden;
    background: var(--backdrop);
  }
  .letterhead {
    position: absolute; left: 86px; top: 14px;
    width: 828px; height: 1170px;
    background: linear-gradient(to bottom, var(--paper) 0, var(--paper) 1000px, var(--footer-wash) 1170px);
    box-shadow: 0 2px 10px rgba(0,0,0,0.25);
  }
  .brand-mark {
    position: absolute; left: 194px; top: 36px;
    width: 60px; height: 60px; border-radius: 50%;
    background: var(--brand-mid);
  }
  .brand-name {
    position: absolute; left: 46px; top: 116px;
    font-family: "Cinzel", serif; font-weight: 600;
    font-size: 17px; letter-spacing: 0.6px;
    color: var(--brand-deep); text-transform: uppercase;
    white-space: nowrap;
  }
  .contact-list {
    position: absolute; right: 32px; top: 50px;
    list-style: none; text-align: right;
    font-family: "Arimo", sans-serif; font-size: 14px;
    color: var(--ink-soft);
  }
  .contact-list li {
    height: 22px; line-height: 22px;
    display: flex; justify-content: flex-end; align-items: center; gap: 6px;
  }
  .contact-list svg { width: 11px; height: 11px; fill: var(--brand-deep); }
  .rule {
    position: absolute; left: 34px; width: 762px; height: 1px;
    background: var(--rule);
  }
  .rule--header { top: 151px; }
  .rule--footer { top: 1089px; }
  .specialist-seal {
    position: absolute; left: 321px; top: 494px;
    width: 184px; height: 184px; border-radius: 50%;
    border: 5px solid var(--seal-ring);
  }
  .footer {
    position: absolute; left: 0; top: 1097px; width: 100%;
    text-align: center;
  }
  .footer__notice {
    font-family: "Questrial", sans-serif; font-size: 17px;
    color: var(--ink); line-height: 22px;
  }
  .footer__address, .footer__web {
    font-family: "Arimo", sans-serif; font-size: 17px;
    color: var(--brand-mid); line-height: 22px;
  }
</style>
</head>
<body>
  <main class="letterhead">
    <header>
      <div class="brand-mark"></div>
      <div class="brand-name">KorvaLex Injury Solicitors</div>
      <ul class="contact-list">
        <li>9317-5802
          <svg viewBox="0 0 12 12" aria-hidden="true"><path d="M2.5 0.8 L4.4 0.6 L5.2 3.2 L3.9 4.2 Q5 6.8 7.6 8.1 L8.7 6.8 L11.3 7.6 L11.2 9.5 Q10.6 11.4 8.6 11.1 Q2 9.6 0.9 3 Q0.7 1.2 2.5 0.8 Z"/></svg>
        </li>
        <li>9581-3274
          <svg viewBox="0 0 12 12" aria-hidden="true"><rect x="0.5" y="3" width="11" height="4" rx="1.5"/><rect x="2.5" y="6" width="7" height="5" rx="0.8"/><rect x="3" y="0.5" width="6" height="3"/></svg>
        </li>
        <li>0438-615-249
          <svg viewBox="0 0 12 12" aria-hidden="true"><path d="M3 0.5 H9 V11.5 H3 Z M4 1.8 V7 H8 V1.8 Z M4 8 V9 H5 V8 Z M5.5 8 V9 H6.5 V8 Z M7 8 V9 H8 V8 Z M4 9.6 V10.6 H8 V9.6 Z" fill-rule="evenodd"/></svg>
        </li>
        <li>mt@korvalex.com.au
          <svg viewBox="0 0 12 12" aria-hidden="true"><path d="M0.5 2 H11.5 V10 H0.5 Z M1.5 3 L6 6.8 L10.5 3 Z M1.5 4.3 V9 H10.5 V4.3 L6 8 Z" fill-rule="evenodd"/></svg>
        </li>
      </ul>
    </header>
    <div class="rule rule--header"></div>

    <div class="specialist-seal"></div>

    <div class="rule rule--footer"></div>
    <footer class="footer">
      <p class="footer__notice">Liability limited by a scheme approved under the Professional Standards Legislation</p>
      <p class="footer__address">P.O. Box B418 Marrowdale South NSW 2291</p>
      <p class="footer__web">www.korvalex.com.au</p>
    </footer>
  </main>
</body>
</html>
```